Business Card Design

Business Card for professional consulting firm working with large financial institutions.

Target Market(s)

Executive buyers

Industry/Entity Type

Banking

Contact Information for Business Card

Mild creativity wanted. Not boring, but do elaborate artwork.

Font styles to use
Serif
Sans Serif

Colors

Designer to choose colors to be used in the design.

Requirements
Must have
• Standard business card features - company name, individual name, telephone, website, email, locations.
Nice to have
• Two colors
Should not have
• too many colors, fancy printing, cartoons.

```html
<!DOCTYPE html>
<html lang="en">
<head>
<meta charset="utf-8">
<title>Northvale Advisory – Business Card</title>
<link href="https://fonts.googleapis.com/css2?family=Noto+Serif:wght@400&family=Open+Sans:wght@400;700&display=swap" rel="stylesheet">
<style>
  :root {
    --page-bg: #3a3a3a;
    --card-bg: #1f1f20;
    --emboss: #2c2c2d;
    --text-light: #f2f2f2;
    --text-muted: #c9c9c9;
    --strip-light: #bdbdbd;
    --tab-grey: #3d4342;
  }
  * { margin: 0; padding: 0; box-sizing: border-box; }
  html, body {
    width: 799px;
    height: 1200px;
    overflow: hidden;
    background: var(--page-bg);
  }
  .sheet {
    position: relative;
    width: 799px;
    height: 1200px;
  }
  .card {
    position: absolute;
    left: 80px;
    width: 640px;
    height: 366px;
    background: var(--card-bg);
    border-radius: 3px;
    overflow: hidden;
    box-shadow: 0 10px 30px rgba(0,0,0,0.45);
  }
  .card--front { top: 150px; }
  .card--back { top: 690px; }

  .brand {
    font-family: "Noto Serif", serif;
    font-weight: 400;
    letter-spacing: 0.5px;
    white-space: nowrap;
  }
  .card--front .brand {
    position: absolute;
    left: 0; right: 0;
    top: 158px;
    text-align: center;
    font-size: 38px;
    color: var(--emboss);
  }
  .card--back .brand {
    position: absolute;
    left: 120px;
    top: 62px;
    font-size: 36px;
    color: var(--text-light);
  }

  .person {
    position: absolute;
    left: 40px;
    top: 206px;
    font-family: "Open Sans", sans-serif;
  }
  .person__name {
    font-size: 22px;
    font-weight: 700;
    color: var(--text-light);
  }
  .person__title {
    font-family: "Noto Serif", serif;
    font-size: 14px;
    color: var(--text-muted);
    margin-top: 2px;
  }

  .contact {
    position: absolute;
    left: 370px;
    top: 190px;
    font-family: "Noto Serif", serif;
    font-size: 14px;
    line-height: 21px;
    color: var(--text-light);
  }
  .contact__address { margin-left: 26px; margin-bottom: 6px; }
  .contact__row { display: flex; align-items: center; gap: 10px; }
  .contact__icon { width: 16px; height: 14px; flex: none; }

  .strip-light {
    position: absolute;
    left: 0;
    top: 300px;
    width: 340px;
    height: 14px;
    background: var(--strip-light);
  }
  .tab {
    position: absolute;
    left: 330px;
    top: 300px;
    width: 310px;
    height: 66px;
    background: var(--tab-grey);
    border-top-left-radius: 26px;
    display: flex;
    align-items: center;
    justify-content: center;
    font-family: "Noto Serif", serif;
    font-size: 15px;
    color: var(--text-light);
  }
</style>
</head>
<body>
<main class="sheet">

  <section class="card card--front" aria-label="Card front">
    <div class="brand">Northvale Advisory</div>
  </section>

  <section class="card card--back" aria-label="Card back">
    <div class="brand">Northvale Advisory</div>

    <div class="person">
      <div class="person__name">John Doe Smith</div>
      <div class="person__title">Managing Director</div>
    </div>

    <div class="contact">
      <div class="contact__address">234 Anywhere St., Any City,<br>Any Town, US 123456</div>
      <div class="contact__row">
        <svg class="contact__icon" viewBox="0 0 16 14" aria-hidden="true">
          <path d="M1 4 Q8 -1 15 4 L13 6 L11 4.5 L5 4.5 L3 6 Z" fill="#f2f2f2"/>
          <rect x="3" y="6.5" width="10" height="7" rx="1" fill="#f2f2f2"/>
          <circle cx="8" cy="10" r="1.8" fill="#1f1f20"/>
        </svg>
        <span>555.555.5555</span>
      </div>
      <div class="contact__row">
        <svg class="contact__icon" viewBox="0 0 16 14" aria-hidden="true">
          <rect x="1" y="2" width="14" height="10" fill="#f2f2f2"/>
          <path d="M1 2 L8 8 L15 2" fill="none" stroke="#1f1f20" stroke-width="1.2"/>
        </svg>
        <span>johndoe@example.com</span>
      </div>
    </div>

    <div class="strip-light"></div>
    <div class="tab">www.yourwebsite.com</div>
  </section>

</main>
</body>
</html>
```